Heron Property Inspection business card

I am the principal inspector of Heron Property Inspections. I serve Northern Virginia from Winchester to Arlington.Associate, Federated Guild of Dwelling Examiners (FGDE)Graduate, FGDE Home Inspectors CourseNational Association of Home Inspectors ExamI'd like the business card to look more professional than comical.I pulled the attached picture off the web. I'd like to have something like that or an image of a house as my logo on the cards.

Target Market(s)

Persons who recently purchased a home.

Industry/Entity Type

Business

Contact Information for Business Card

Bob AllenBadger Home Inspections, LLC.4455 River RoadBluemont, Virginia 20135cell: 703-231-6680e-mail: tkmarlow@postvale.net

Font styles to use
Serif
Sans Serif

Requirements
Must have
• I'd like to have a logo, something that identifies me as a home inspector. The attached images are something that I'd like to have incorporated into my business card logo.
Nice to have
• I'd like a sketch of a house and/or a magnifying glass showing a house being inspected. The attached images are used as a suggestion only, I do not own the images.
Should not have
• Gimmicky stuff. I want to appear professional and trustworthy.

```html
<!DOCTYPE html>
<html lang="en">
<head>
<meta charset="utf-8">
<title>Heron Property Inspections – Business Card</title>
<link rel="stylesheet" href="https://fonts.googleapis.com/css2?family=Alegreya:wght@400&family=Arimo:wght@400&display=swap">
<style>
  :root {
    --brand-blue: #29abe2;
    --ink: #231f20;
    --text-grey: #2b2b2b;
    --card-white: #ffffff;
    --backdrop: #e8ebee;
  }
  html, body {
    margin: 0;
    width: 1200px;
    height: 902px;
    overflow: hidden;
    background: var(--backdrop);
  }
  .canvas {
    position: relative;
    width: 1200px;
    height: 902px;
  }
  .card {
    position: absolute;
    left: 60px;
    top: 143px;
    width: 940px;
    height: 535px;
    transform: scale(1.15);
    transform-origin: top left;
    background: var(--card-white);
    border-radius: 24px;
    overflow: hidden;
    box-shadow: 0 8px 24px rgba(0,0,0,0.12);
  }
  .card-swoosh {
    position: absolute;
    inset: 0;
    width: 940px;
    height: 535px;
  }
  .swoosh-fill { fill: var(--brand-blue); }
  .swoosh-line { fill: var(--ink); }

  .company-name {
    position: absolute;
    right: 68px;
    top: 160px;
    display: flex;
    align-items: center;
    margin: 0;
    font-family: "Alegreya", Georgia, serif;
    font-weight: 400;
    font-size: 34px;
    line-height: 40px;
    color: var(--ink);
    white-space: nowrap;
  }
  .company-square {
    width: 18px;
    height: 18px;
    margin-right: 14px;
    background: var(--brand-blue);
    flex: none;
  }

  .person {
    position: absolute;
    left: 38px;
    top: 282px;
  }
  .person-name {
    margin: 0;
    font-family: "Alegreya", Georgia, serif;
    font-weight: 400;
    font-size: 41px;
    line-height: 48px;
    color: var(--brand-blue);
  }
  .person-title {
    margin: 0;
    font-family: "Arimo", Arial, sans-serif;
    font-size: 24px;
    line-height: 26px;
    color: var(--text-grey);
  }

  .contact-list {
    position: absolute;
    left: 38px;
    top: 390px;
    margin: 0;
    padding: 0;
    list-style: none;
    font-family: "Arimo", Arial, sans-serif;
    font-size: 25px;
    color: var(--text-grey);
  }
  .contact-item {
    display: flex;
    align-items: center;
    height: 35px;
  }
  .contact-icon {
    width: 27px;
    height: 27px;
    margin-right: 28px;
    flex: none;
  }
  .icon-tile { fill: var(--brand-blue); }
  .icon-glyph { fill: none; stroke: #fff; stroke-width: 1.8; stroke-linecap: round; stroke-linejoin: round; }
  .icon-glyph-solid { fill: #fff; }
</style>
</head>
<body>
<main class="canvas">
  <article class="card">
    <svg class="card-swoosh" viewBox="0 0 940 535" aria-hidden="true">
      <path class="swoosh-fill" d="M0 0 H228 C125 35 35 115 9 218 H0 Z"/>
      <path class="swoosh-line" d="M4 212 C30 108 112 32 210 4 C122 42 46 118 12 212 Z"/>
      <path class="swoosh-fill" d="M940 295 C905 415 825 497 715 535 H940 Z"/>
      <path class="swoosh-line" d="M728 530 C830 490 902 420 936 322 C912 432 834 505 742 535 Z"/>
    </svg>

    <p class="company-name"><span class="company-square" aria-hidden="true"></span>Heron Property Inspections, LLC</p>

    <div class="person">
      <h1 class="person-name">Employee Name</h1>
      <p class="person-title">Managing Director</p>
    </div>

    <ul class="contact-list">
      <li class="contact-item">
        <svg class="contact-icon" viewBox="0 0 27 27" aria-hidden="true">
          <rect class="icon-tile" width="27" height="27" rx="4"/>
          <path class="icon-glyph-solid" d="M8 5.5 L10.8 5 L12.6 9.4 L10.6 11 C11.6 13.3 13.5 15.3 16 16.4 L17.6 14.4 L22 16.2 L21.5 19 C21.2 20.3 19.9 21.2 18.6 21 C11.8 20 7 15.2 6 8.4 C5.8 7 6.7 5.8 8 5.5 Z"/>
        </svg>
        <span>703-555-0192</span>
      </li>
      <li class="contact-item">
        <svg class="contact-icon" viewBox="0 0 27 27" aria-hidden="true">
          <rect class="icon-tile" width="27" height="27" rx="4"/>
          <rect class="icon-glyph" x="5" y="8" width="17" height="12" rx="1"/>
          <path class="icon-glyph" d="M5.5 8.5 L13.5 15 L21.5 8.5 M5.5 19.5 L11 14 M21.5 19.5 L16 14"/>
        </svg>
        <span>tkmarlow@postvale.net</span>
      </li>
      <li class="contact-item">
        <svg class="contact-icon" viewBox="0 0 27 27" aria-hidden="true">
          <rect class="icon-tile" width="27" height="27" rx="4"/>
          <path class="icon-glyph" d="M13.5 22 C9 16.5 7.5 13.5 7.5 11 A6 6 0 0 1 19.5 11 C19.5 13.5 18 16.5 13.5 22 Z"/>
          <circle class="icon-glyph" cx="13.5" cy="11" r="2.2"/>
        </svg>
        <span>7182 Quarry LaneFernhill, Virginia 20148</span>
      </li>
    </ul>
  </article>
</main>
</body>
</html>
```